Redesign of business card for Cedar Ridge Mechanical

We are looking for a new design for our business cards for Cedar Ridge Mechanical. We are a plumbing & HVAC construction company, operating on the West Coast of Canada and USA. Logo attached.
Industry/Entity Type
Construction - Plumbing & HVAC
Contact Information for Business Card
Name, address, phone numbers, email, website address
Look and feel
Each slider illustrates characteristics of the customer's brand and the style your logo design should communicate.

```html
<!DOCTYPE html>
<html lang="en">
<head>
<meta charset="utf-8">
<title>Cedar Ridge Mechanical – Business Card</title>
<link rel="stylesheet" href="https://fonts.googleapis.com/css2?family=Montserrat:wght@400;500;700&display=swap">
<style>
  :root {
    --page-bg: #d8d2ca;
    --card-light: #ece5dc;
    --card-light-2: #ddd3c7;
    --ink: #1b1a19;
    --ink-soft: #2a2826;
    --night: #0d0d0d;
    --gold-text: #dcc9a9;
  }
  * { box-sizing: border-box; margin: 0; padding: 0; }
  html, body {
    width: 1200px; height: 1047px; overflow: hidden;
    background: var(--page-bg);
    font-family: "Montserrat", sans-serif;
  }
  .business-card {
    position: absolute; left: 100px; top: 250px;
    width: 1000px; height: 545px;
    border-radius: 26px; overflow: hidden;
    background: linear-gradient(160deg, var(--card-light) 0%, var(--card-light-2) 100%);
    box-shadow: 0 18px 40px rgba(0,0,0,0.18);
  }
  .card-panel { position: absolute; inset: 0; width: 100%; height: 100%; }
  .card-panel .dark-field { fill: var(--night); }
  .brand { position: absolute; left: 44px; top: 60px; display: flex; align-items: center; gap: 22px; }
  .brand-square { width: 64px; height: 64px; background: var(--ink); }
  .brand-name {
    font-weight: 700; font-size: 38px; line-height: 1.12;
    color: var(--ink); text-transform: uppercase; letter-spacing: 1px;
  }
  .holder { position: absolute; right: 40px; top: 48px; text-align: right; }
  .holder-name { font-weight: 700; font-size: 34px; letter-spacing: 1.5px; color: var(--ink); }
  .holder-title { font-weight: 500; font-size: 24px; color: var(--ink-soft); margin-top: 8px; }
  .accent-bar { position: absolute; right: 0; top: 59px; width: 13px; height: 68px; background: var(--ink); }
  .contact {
    position: absolute; right: 40px; top: 300px; text-align: right;
    color: var(--gold-text); font-size: 24px; font-weight: 400;
  }
  .contact-address p { line-height: 38px; }
  .contact-list { list-style: none; margin-top: 30px; }
  .contact-list li { display: flex; justify-content: flex-end; align-items: center; gap: 10px; line-height: 38px; }
  .contact-icon { width: 20px; height: 20px; }
</style>
</head>
<body>
  <section class="business-card">
    <svg class="card-panel" viewBox="0 0 1000 545" preserveAspectRatio="none" aria-hidden="true">
      <path class="dark-field" d="M0,480 C350,480 650,260 1000,225 L1000,545 L0,545 Z"/>
    </svg>

    <div class="brand">
      <span class="brand-square"></span>
      <span class="brand-name">Cedar Ridge<br>Mechanical</span>
    </div>

    <div class="holder">
      <h1 class="holder-name">DANIEL HART</h1>
      <p class="holder-title">Managing Director</p>
    </div>
    <span class="accent-bar"></span>

    <div class="contact">
      <div class="contact-address">
        <p>Your address, City</p>
        <p>State, Zip 1234</p>
      </div>
      <ul class="contact-list">
        <li>123 456 789
          <svg class="contact-icon" viewBox="0 0 24 24"><path fill="#dcc9a9" d="M6.6 10.8a15.1 15.1 0 0 0 6.6 6.6l2.2-2.2a1 1 0 0 1 1-.25 11.4 11.4 0 0 0 3.6.57 1 1 0 0 1 1 1V20a1 1 0 0 1-1 1A17 17 0 0 1 3 4a1 1 0 0 1 1-1h3.5a1 1 0 0 1 1 1c0 1.25.2 2.45.57 3.57a1 1 0 0 1-.25 1z"/></svg>
        </li>
        <li>info@cedarridgemech.com
          <svg class="contact-icon" viewBox="0 0 24 24"><rect x="2" y="5" width="20" height="14" rx="2" fill="#dcc9a9"/><path d="M3 6.5l9 6.5 9-6.5" fill="none" stroke="#0d0d0d" stroke-width="1.6"/></svg>
        </li>
        <li>www.cedarridgemech.com
          <svg class="contact-icon" viewBox="0 0 24 24"><circle cx="12" cy="12" r="9.5" fill="none" stroke="#dcc9a9" stroke-width="1.8"/><ellipse cx="12" cy="12" rx="4" ry="9.5" fill="none" stroke="#dcc9a9" stroke-width="1.5"/><path d="M2.5 12h19" stroke="#dcc9a9" stroke-width="1.5"/></svg>
        </li>
      </ul>
    </div>
  </section>
</body>
</html>
```